packaging design for disposable trash bag

We need 3 design for 3 of our products. first item is trash bag,the second item is disposable table cover and third is food packaging bag . We are a company in Singapore selling disposable product. This packaging products will be sold on shelf or online.

Attached is the requirement of the product. And some samples.

Target Market(s)

adult, most likely housewife

Requirements
Must have
• Packing design requirement for trash bag
• 1. Include company logo design, which is attached in the creative brief. DARVELLO POLYMER.
• 2. Clear showing of the product and its illustration of using. Eg. The trash bin.
• 3. Allocate a box for the purpose of sticking product size sticker.
• 4. Each packing bag holds 10pcs
• 5. Show of country of origin. Product of Singapore.
• 6. Use of one colour for printing of packing bag ( Black / blue/ bright Green/ white )
• 7. Show of warning: Keep polythene bags away from young children
• 8. dimension of the packagaing printing area : Lenght : 20 cm , Height 26 cm
• Packing design requirement for disposable Table Cover
• 1. Include company logo design, which is attached in the creative brief. Our company is DARVELLO POLYMER.
• 2. Clear showing of the product and its illustration of using. Eg. The table?.
• 4. Each packing bag holds 5pcs
• 6. Use of one colour for printing of the packing bag ( Black / blue/ bright Green )
• Packing design requirement for disposable food packaging plastic bag
• 2. Clear showing of the product and its illustration of using. Eg. Food?.
• 4. Show of country of origin. Product of Singapore.
• 5. Use of one colour for printing of the packing bag ( Black/ bright green )
• 6. Show of warning: Keep polythene bags away from young children
• 7. Show of product information: hygienic, food grade, freezer resistance, grease proof, damp proof, heat resistant.
• 8. Include the open here packing opening.
• 9. dimension of the packagaing printing area : Lenght : 15 cm , Height 22 cm
Nice to have
• requirement is stated in the must have. Good to allocate some space beside the packaging PCS area for promotion stickers . And also space allocated for bar code stickers.
Should not have
• no more than one color for printing

```html
<!DOCTYPE html>
<html lang="en">
<head>
<meta charset="UTF-8">
<title>Darvello Polymer – Garbage Bag Packaging</title>
<link href="https://fonts.googleapis.com/css2?family=Anton&family=Archivo+Narrow:wght@400;700&family=Arimo:wght@400;700&display=swap" rel="stylesheet">
<style>
  :root {
    --ink: #1f9a4a;
    --film: #c9cfdd;
    --page: #eef0f4;
  }
  * { box-sizing: border-box; margin: 0; padding: 0; }
  html, body { width: 918px; height: 1200px; overflow: hidden; background: var(--page); }
  .pack {
    position: absolute; left: 29px; top: 27px; width: 860px; height: 1146px;
    background: var(--film); border: 3px solid var(--ink); border-radius: 8px;
    font-family: "Arimo", sans-serif; color: var(--ink); overflow: hidden;
  }

  /* brand block */
  .brand {
    position: absolute; left: 0; top: 0; width: 442px; height: 287px;
    border-bottom: 8px solid var(--ink);
  }
  .brand-square { position: absolute; left: 173px; top: 40px; width: 96px; height: 96px; background: var(--ink); }
  .brand-name {
    position: absolute; left: 0; right: 0; top: 166px; text-align: center;
    font-size: 39px; line-height: 1.18; font-weight: 400; letter-spacing: -0.5px;
  }

  /* size sticker box */
  .size-box {
    position: absolute; left: 442px; top: 20px; right: 0; height: 348px; z-index: 2;
    background: var(--film);
    border: 16px solid var(--ink); border-right: 0; border-bottom-width: 20px;
  }
  .qty-label {
    position: absolute; left: 22px; top: 16px;
    font-weight: 700; font-size: 19px; line-height: 1.02; letter-spacing: 0.8px;
  }
  .qty-value {
    position: absolute; left: 153px; top: 6px;
    font-family: "Anton", sans-serif; font-size: 76px; line-height: 1;
    transform: scaleX(0.86); transform-origin: left top; white-space: nowrap;
  }
  .corner { position: absolute; width: 36px; height: 36px; border-color: var(--ink); border-style: solid; border-width: 0; }
  .tl { border-top-width: 5px; border-left-width: 5px; }
  .tr { border-top-width: 5px; border-right-width: 5px; }
  .bl { border-bottom-width: 5px; border-left-width: 5px; }
  .br { border-bottom-width: 5px; border-right-width: 5px; }
  .size-label { position: absolute; left: 0; right: 0; top: 182px; text-align: center; font-weight: 700; font-size: 25px; }

  /* main product block */
  .hero {
    position: absolute; left: 19px; top: 287px; right: 0; height: 486px;
    border: 10px solid var(--ink); border-right: 0; border-bottom-width: 14px;
  }
  .title {
    position: absolute; left: 12px; top: 50px; font-family: "Anton", sans-serif;
    font-size: 186px; line-height: 1; font-weight: 400; text-transform: uppercase;
    transform: scaleX(0.6); transform-origin: left top; white-space: nowrap;
  }
  .bins {
    position: absolute; left: 422px; top: 128px; width: 398px; height: 256px;
    background: linear-gradient(180deg, #2aa857, var(--ink)); border-radius: 6px;
  }
  .bins-note {
    position: absolute; left: 438px; top: 398px;
    font-weight: 700; font-size: 18px; letter-spacing: 1.1px; white-space: nowrap;
  }

  /* sticker + disposal block */
  .info {
    position: absolute; left: 0; top: 773px; right: 0; height: 297px;
    border-top: 4px solid var(--ink); border-right: 18px solid var(--ink); border-bottom: 16px solid var(--ink);
  }
  .sticker-area { position: absolute; left: 33px; top: 51px; width: 373px; height: 194px; }
  .sticker-label { position: absolute; left: 0; right: 0; top: 82px; text-align: center; font-weight: 700; font-size: 25px; }
  .disposal {
    position: absolute; left: 422px; top: 40px; width: 400px; text-align: center;
    font-weight: 700; font-size: 22.5px; line-height: 1.25; letter-spacing: 0.3px;
  }
  .marks { position: absolute; left: 566px; top: 192px; width: 132px; height: 56px; background: var(--ink); border-radius: 28px; opacity: 0.85; }

  /* footer */
  .warning { position: absolute; left: 0; right: 0; top: 1074px; text-align: center; }
  .warning-line { font-family: "Archivo Narrow", sans-serif; font-weight: 700; font-size: 24px; line-height: 1.2; white-space: nowrap; }
  .warning-line strong { font-family: "Arimo", sans-serif; font-size: 28px; letter-spacing: 0.5px; }
  .origin { font-family: "Archivo Narrow", sans-serif; font-weight: 400; font-size: 27px; line-height: 1.2; margin-right: 20px; }
</style>
</head>
<body>
<main class="pack">
  <section class="brand">
    <div class="brand-square"></div>
    <p class="brand-name">DARVELLO POLYMER<br>PTE LTD</p>
  </section>

  <section class="hero">
    <h1 class="title">Garbage<br>Bag</h1>
    <div class="bins" role="img" aria-label="Illustration of three types of rubbish bins"></div>
    <p class="bins-note">SUITABLE FOR ALL TYPES OF BINS</p>
  </section>

  <section class="size-box">
    <span class="qty-label">CONTENT<br>QUANTITY</span>
    <span class="qty-value">10 PIECES</span>
    <span class="corner tl" style="left:16px;top:102px"></span>
    <span class="corner tr" style="right:4px;top:102px"></span>
    <span class="corner bl" style="left:16px;bottom:15px"></span>
    <span class="corner br" style="right:4px;bottom:15px"></span>
    <p class="size-label">SIZE (DIMENSION)</p>
  </section>

  <section class="info">
    <div class="sticker-area">
      <span class="corner tl" style="left:0;top:0"></span>
      <span class="corner tr" style="right:0;top:0"></span>
      <span class="corner bl" style="left:0;bottom:0"></span>
      <span class="corner br" style="right:0;bottom:0"></span>
      <p class="sticker-label">BARCODE</p>
    </div>
    <p class="disposal">USED BAGS SHOULD BE TIED<br>PROPERLY BEFORE DISPOSAL<br>TO ENSURE CLEANLINESS<br>TO THE SURROUNDING<br>ENVIRONMENT.</p>
    <div class="marks" role="img" aria-label="Recycling and disposal marks"></div>
  </section>

  <footer class="warning">
    <p class="warning-line"><strong>WARNING:</strong> PLEASE KEEP POLYTHENE BAGS AWAY FROM YOUNG CHILDREN</p>
    <p class="origin">PRODUCT OF SINGAPORE</p>
  </footer>
</main>
</body>
</html>
```